Northfield Builders Guild Business card

We are looking for a new business card design with photo included.
Our business is a nonprofit construction contractor membership organization. We offer business education, assist with business setup and licensing, provide safety training, and provide a member directory.
URL: www.builderslinkguild.org
Color code:
CMYK: 0 cyan, 42 magenta, 100 yellow, 0 black for Print.
Hexidecimal: #FF9900
RGB: R 255; G 153; B 0

```html
<!DOCTYPE html>
<html lang="en">
<head>
<meta charset="utf-8">
<title>Northfield Builders Guild – Business Card</title>
<link rel="stylesheet" href="https://fonts.googleapis.com/css2?family=Montserrat:wght@800&family=Oswald:wght@500&family=Open+Sans:wght@400&display=swap">
<style>
  :root {
    --backdrop: #2a2a2a;
    --paper: #ffffff;
    --brand-orange: #f79c1f;
    --ink-dark: #333333;
    --ink-text: #2b2b2b;
  }
  * { margin: 0; padding: 0; box-sizing: border-box; }
  html, body { width: 1200px; height: 751px; overflow: hidden; }
  body { background: var(--backdrop); position: relative; font-family: "Open Sans", sans-serif; }

  .card {
    position: absolute;
    left: 360px;
    width: 493px;
    height: 282px;
    background: var(--paper);
    box-shadow: 0 2px 6px rgba(0,0,0,0.45);
    overflow: hidden;
  }
  .card--front { top: 90px; }
  .card--back { top: 396px; }

  .wordmark {
    position: absolute;
    left: 0; right: 0;
    text-align: center;
    font-family: "Montserrat", sans-serif;
    font-weight: 800;
    color: var(--ink-dark);
    text-transform: uppercase;
    line-height: 1.02;
  }
  .card--front .wordmark { top: 52px; font-size: 25px; }
  .card--back .wordmark { top: 108px; font-size: 28px; }

  .name-band { position: absolute; left: 0; top: 154px; width: 493px; height: 52px; }

  .holder-name {
    position: absolute; left: 17px; top: 163px;
    font-family: "Oswald", sans-serif; font-weight: 500;
    font-size: 19px; color: var(--ink-dark); letter-spacing: -0.2px;
    text-transform: uppercase;
  }
  .holder-title {
    position: absolute; left: 16px; top: 187px;
    font-size: 7.5px; letter-spacing: 2.1px; color: var(--ink-dark);
  }

  .contacts { position: absolute; right: 21px; top: 181px; list-style: none; }
  .contacts li {
    display: flex; align-items: center; justify-content: flex-end;
    height: 22px; margin-bottom: 5px;
    font-size: 12.5px; color: var(--ink-text);
  }
  .contacts svg { width: 22px; height: 22px; margin-left: 6px; flex: none; }

  .website {
    position: absolute; left: 0; right: 0; top: 251px;
    text-align: center; font-size: 12.5px; letter-spacing: 5.6px; color: var(--ink-text);
  }
</style>
</head>
<body>
  <section class="card card--front">
    <div class="wordmark">Northfield<br>Builders Guild</div>

    <svg class="name-band" viewBox="0 0 493 52" aria-hidden="true">
      <polygon points="0,0 232,0 198,47 0,47" fill="var(--brand-orange)"/>
      <rect x="232" y="0" width="261" height="3" fill="var(--brand-orange)"/>
      <polyline points="3,48 198,48 233,3.5 493,3.5" fill="none" stroke="var(--ink-dark)" stroke-width="2"/>
    </svg>

    <div class="holder-name">Dana Whitford</div>
    <div class="holder-title">CEO/Managing Director</div>

    <ul class="contacts">
      <li>555-014-2288
        <svg viewBox="0 0 22 22" aria-hidden="true"><circle cx="11" cy="11" r="11" fill="var(--brand-orange)"/><path d="M7.5 5.5l2 0 1 3-1.4 1.2a7 7 0 0 0 3.2 3.2l1.2-1.4 3 1v2a1.5 1.5 0 0 1-1.6 1.5A10 10 0 0 1 6 7.1 1.5 1.5 0 0 1 7.5 5.5z" fill="#fff"/></svg>
      </li>
      <li>555-014-2288
        <svg viewBox="0 0 22 22" aria-hidden="true"><circle cx="11" cy="11" r="11" fill="var(--brand-orange)"/><path d="M4.5 11.5L11 5l6.5 6.5M6.5 10v7h3.2v-4h2.6v4h3.2v-7" fill="none" stroke="#fff" stroke-width="1.5" stroke-linejoin="round"/></svg>
      </li>
      <li>dana.whitford@builderslinkguild.org
        <svg viewBox="0 0 22 22" aria-hidden="true"><circle cx="11" cy="11" r="11" fill="var(--brand-orange)"/><rect x="5" y="7" width="12" height="8.5" fill="none" stroke="#fff" stroke-width="1.2"/><path d="M5 7l6 5 6-5M5 15.5l4.3-4M17 15.5l-4.3-4" fill="none" stroke="#fff" stroke-width="1.2"/></svg>
      </li>
    </ul>
  </section>

  <section class="card card--back">
    <div class="wordmark">Northfield<br>Builders Guild</div>
    <div class="website">www.builderslinkguild.org</div>
  </section>
</body>
</html>
```